Thriller/Romance novel book cover design - Copper Tidewake

I need a book cover for a novel (print + ebook). Genre = thriller / romance. Title = Copper Tidewake. Author = Dorian Kell.
Story is set in Caribbean. 45-year-old Ex-OVK agent is hunted by corrupt politicians, OVK and cartel. He is a life-long fisherman and seaman who joined the Army after college and became a war hero, followed by 10 years as operative for the OVK. Betrayal from Washington saw him accused of killing his mentor/friend/OVK Director and he is now a fugitive. He has been hiding for 7 years on Grand Cayman, and lives a secluded, private life as a fisherman on his modern sportfisherman-style boat ('50 Velmora Convertible for reference). Boat name = Copper Tidewake (as in the playing card) represents fate to him and his high school sweetheart to whom he was engaged before a tragic event separated them. His main goal, beyond survival, is to reunite with his long, lost love, but he can't risk putting her in danger until he settles the case and those searching for him. The boat name (Copper Tidewake) only has relevance to him and his soulmate, who is not even aware that he is still alive.

Target Market(s)

thriller and romantic thriller readers

Requirements
Must have
• author name should be small on bottom of cover - not at top. Design is wide open for creative ideas. If a boat is used in artwork, it must be a modern sportfisherman style boat (google will define this
Nice to have
• I like intrigue and mystery. Don't try to explain or show too much. Prefer sunsets (orange, red, purple, yellow) to blue sky, blue water to give it a darker tone
Should not have
• do not want images of people on the cover like many romance novels do.

```html
<!DOCTYPE html>
<html lang="en">
<head>
<meta charset="utf-8">
<title>Copper Tidewake — Dorian Kell</title>
<link rel="stylesheet" href="https://fonts.googleapis.com/css2?family=Sorts+Mill+Goudy&family=Cormorant+Garamond:wght@500&display=swap">
<style>
  :root {
    --page: #ffffff;
    --night: #0d1c47;
    --violet: #3f2a74;
    --mauve: #8b5e9c;
    --ember: #e3303a;
    --amber: #f2883a;
    --gold: #f7c63c;
    --sea-deep: #2e1a2a;
    --sea-glow: #b8542c;
    --ink: #ffffff;
    --pip: #141014;
    --card-edge: rgba(40, 20, 40, 0.35);
  }
  html, body {
    margin: 0;
    width: 1200px;
    height: 1200px;
    overflow: hidden;
    background: var(--page);
  }
  .book-cover {
    position: absolute;
    left: 240px;
    top: 60px;
    width: 720px;
    height: 1127px;
    overflow: hidden;
  }
  .sunset-scene {
    position: absolute;
    inset: 0;
    background:
      linear-gradient(180deg,
        var(--night) 0%,
        var(--violet) 22%,
        var(--mauve) 44%,
        #b0507a 52%,
        var(--ember) 58%,
        var(--amber) 66%,
        var(--gold) 74%,
        #f4a640 77%,
        var(--sea-glow) 78%,
        #7a3530 86%,
        var(--sea-deep) 100%);
  }
  .title {
    position: absolute;
    left: 0;
    right: 0;
    margin: 0;
    text-align: center;
    font-family: "Sorts Mill Goudy", "Goudy Old Style", serif;
    font-weight: 400;
    color: var(--ink);
    text-shadow: 0 3px 6px rgba(0, 0, 0, 0.45);
    line-height: 1;
  }
  .title-line-top {
    top: 62px;
    font-size: 160px;
    letter-spacing: 2px;
  }
  .title-line-main {
    top: 212px;
    font-size: 168px;
    letter-spacing: -2px;
  }
  .playing-card {
    position: absolute;
    left: 193px;
    top: 373px;
    width: 337px;
    height: 477px;
  }
  .author {
    position: absolute;
    left: 0;
    right: 0;
    top: 990px;
    margin: 0;
    text-align: center;
    font-family: "Cormorant Garamond", "Garamond", serif;
    font-weight: 500;
    font-size: 62px;
    letter-spacing: 5px;
    color: var(--ink);
    text-shadow: 0 2px 4px rgba(0, 0, 0, 0.4);
  }
</style>
</head>
<body>
  <main class="book-cover">
    <div class="sunset-scene" role="img" aria-label="Photograph of a fiery Caribbean sunset over calm sea with a modern sportfisherman boat named Copper Tidewake anchored in the foreground and a bullet hole piercing the sky"></div>

    <h1 class="title title-line-top">Copper</h1>
    <h1 class="title title-line-main">Tidewake</h1>

    <svg class="playing-card" viewBox="0 0 337 477" aria-hidden="true">
      <defs>
        <symbol id="club" viewBox="0 0 100 100">
          <circle cx="50" cy="26" r="22"/>
          <circle cx="26" cy="58" r="22"/>
          <circle cx="74" cy="58" r="22"/>
          <rect x="44" y="40" width="12" height="30"/>
          <path d="M50 60 L36 98 L64 98 Z"/>
        </symbol>
      </defs>
      <rect x="1" y="1" width="335" height="475" rx="20" fill="rgba(255,255,255,0.04)" stroke="var(--card-edge)" stroke-width="2"/>
      <g fill="var(--pip)">
        <text x="31" y="73" font-family="Arial, sans-serif" font-size="44" text-anchor="middle">3</text>
        <use href="#club" x="14" y="82" width="34" height="34"/>
        <use href="#club" x="56" y="50" width="66" height="66"/>
        <g transform="rotate(180 168.5 238.5)">
          <text x="31" y="73" font-family="Arial, sans-serif" font-size="44" text-anchor="middle">3</text>
          <use href="#club" x="14" y="82" width="34" height="34"/>
          <use href="#club" x="56" y="50" width="66" height="66"/>
        </g>
      </g>
    </svg>

    <p class="author">Dorian Kell</p>
  </main>
</body>
</html>
```